Business Card Design for company

We want new business cards. We'd like something different-- yet still highly professional. Our tagline is Providing leadership, delivering success. Stock photos are ok, as long as they are relevant and look upscale.

Target Market(s)

Architecture/Business Management Consulting/Engineering Consulting

Contact Information for Business Card

dark gray background with pops of blue might be good, but you tell me. You're the designers. Rounded corners might be nice, but again, you tell me.

Font styles to use
Serif
Sans Serif

Colors
3276b5
5c5c5c
9d9d9d
fbfbfb

Requirements
Nice to have
• Something different, but still very professional.

```html
<!DOCTYPE html>
<html lang="en">
<head>
<meta charset="utf-8">
<title>Norvane Group – Business Cards</title>
<link rel="stylesheet" href="https://fonts.googleapis.com/css2?family=Poppins:ital,wght@0,400;0,500;0,600;1,400&display=swap">
<style>
  :root {
    --stage: #2a2b2d;
    --card: #54585e;
    --card-dark: #474b50;
    --blue: #3276b5;
    --white: #fbfbfb;
    --muted: #d6d8db;
    --rule: #9d9d9d;
  }
  * { box-sizing: border-box; margin: 0; padding: 0; }
  html, body {
    width: 1200px; height: 1139px; overflow: hidden;
    background: var(--stage);
    font-family: "Poppins", sans-serif;
  }
  .stage {
    position: relative; width: 1200px; height: 1139px;
    display: flex; flex-direction: column; align-items: center;
    justify-content: center; gap: 44px;
  }
  .card {
    position: relative; width: 840px; height: 480px;
    background: var(--card);
    border-bottom: 5px solid var(--blue);
    box-shadow: 0 12px 28px rgba(0,0,0,.45);
  }
  /* back side */
  .card--back {
    display: flex; flex-direction: column; align-items: center; justify-content: center;
  }
  .card--back .brand-name {
    font-size: 58px; font-weight: 600; color: var(--card-dark);
    letter-spacing: 2px;
  }
  .card--back .web {
    position: absolute; bottom: 56px; left: 0; right: 0; text-align: center;
    color: var(--muted); font-size: 20px; letter-spacing: 1px;
  }
  /* front side */
  .card--front { display: flex; align-items: center; padding: 0 60px; }
  .front-brand {
    width: 340px; display: flex; align-items: center; gap: 16px;
  }
  .front-brand .mark {
    width: 30px; height: 30px; background: var(--blue); flex: none;
  }
  .front-brand .brand-name {
    font-size: 40px; font-weight: 600; color: var(--white); line-height: 1.15;
  }
  .divider {
    width: 2px; height: 300px; background: var(--rule); margin: 0 34px 0 10px;
  }
  .contact { color: var(--white); }
  .contact .person {
    font-size: 26px; font-weight: 600; color: var(--blue); letter-spacing: 2px;
  }
  .contact .role {
    font-size: 17px; font-style: italic; color: var(--muted); margin-bottom: 20px;
  }
  .contact .address { font-size: 19px; line-height: 1.45; margin-bottom: 20px; }
  .contact ul { list-style: none; font-size: 19px; line-height: 1.6; }
  .contact li { display: flex; align-items: center; gap: 14px; }
  .contact svg { width: 16px; height: 16px; flex: none; }
</style>
</head>
<body>
<main class="stage">
  <section class="card card--back">
    <div class="brand-name">NORVANE GROUP</div>
    <div class="web">www.norvanegroup.com</div>
  </section>

  <section class="card card--front">
    <div class="front-brand">
      <span class="mark"></span>
      <span class="brand-name">Norvane Group</span>
    </div>
    <div class="divider"></div>
    <div class="contact">
      <div class="person">DANIEL HARTLEY</div>
      <div class="role">Resident Manager</div>
      <div class="address">418 W Harbor Ave. Ste 210<br>Easton, VA 23120</div>
      <ul>
        <li>
          <svg viewBox="0 0 16 16" aria-hidden="true"><path d="M3 1h3l1.5 4-2 1.2a9 9 0 0 0 4.3 4.3L11 8.5l4 1.5v3a2 2 0 0 1-2 2A13 13 0 0 1 1 3a2 2 0 0 1 2-2z" fill="var(--blue)"/></svg>
          +1 555.201.0147
        </li>
        <li>
          <svg viewBox="0 0 16 16" aria-hidden="true"><rect x="4" y="1" width="8" height="4" fill="none" stroke="var(--blue)" stroke-width="1.5"/><rect x="1" y="5" width="14" height="7" rx="1" fill="var(--blue)"/><rect x="4" y="10" width="8" height="5" fill="var(--card)" stroke="var(--blue)" stroke-width="1.5"/></svg>
          +1 555.461.0282
        </li>
        <li>
          <svg viewBox="0 0 16 16" aria-hidden="true"><rect x="1" y="3" width="14" height="10" fill="none" stroke="var(--blue)" stroke-width="1.5"/><path d="M1 3l7 6 7-6" fill="none" stroke="var(--blue)" stroke-width="1.5"/></svg>
          info@norvanegroup.com
        </li>
        <li>
          <svg viewBox="0 0 16 16" aria-hidden="true"><circle cx="8" cy="8" r="7" fill="none" stroke="var(--blue)" stroke-width="1.5"/><ellipse cx="8" cy="8" rx="3" ry="7" fill="none" stroke="var(--blue)" stroke-width="1.2"/><path d="M1 8h14" stroke="var(--blue)" stroke-width="1.2"/></svg>
          www.norvanegroup.com
        </li>
      </ul>
    </div>
  </section>
</main>
</body>
</html>
```